Heritage Hollow Business Cards

Require a business card design. <br/><br/>Needs to include logo (either round or long version) plus these details:<br/>Maya Torvell<br/>Heritage Hollow<br/>maya@kelvadtrading.com.au<br/>02 6481 7395<br/>PO Box Glenwarra NSW 2791<br/>www.heritagehollow.com.au<br/><br/>I need in an editable format so that I can create for multiple staff members. <br/><br/>

Target Market(s)

We are an online store selling renovation products to home owners are builders. Looking for a classic classy design.

Industry/Entity Type

Home And Garden

Contact Information for Business Card

Maya Torvell
Heritage Hollow
maya@kelvadtrading.com.au
02 6481 7395
PO Box Glenwarra NSW 2791
www.heritagehollow.com.au

Colors

Designer to choose colors to be used in the design.

Requirements
Must have
• Must include Logo.

```html
<!DOCTYPE html>
<html lang="en">
<head>
<meta charset="utf-8">
<title>Heritage Hollow Business Cards</title>
<link href="https://fonts.googleapis.com/css2?family=Montserrat:wght@400;500;600&display=swap" rel="stylesheet">
<style>
  :root {
    --backdrop: #c8a67c;
    --card-light: #ffffff;
    --card-dark: #0d0e10;
    --ink: #1d1f21;
    --ink-soft: #3a3d40;
    --rule: #5d6b66;
    --sketch-light: #d9d9d9;
    --sketch-dark: #2c2e31;
    --logo-ring-dark: #bfbfbf;
    --white: #ffffff;
  }
  html, body {
    margin: 0;
    padding: 0;
    width: 1200px;
    height: 859px;
    overflow: hidden;
    background: var(--backdrop);
    font-family: "Montserrat", sans-serif;
  }
  .canvas {
    position: relative;
    width: 1200px;
    height: 859px;
  }
  .card {
    position: absolute;
    top: 288px;
    width: 500px;
    height: 285px;
    border-radius: 12px;
    overflow: hidden;
    box-shadow: 0 6px 14px rgba(0,0,0,0.25);
  }
  .card--front { left: 60px; background: var(--card-light); color: var(--ink); }
  .card--back { left: 639px; background: var(--card-dark); }

  .logo {
    position: absolute;
    display: flex;
    align-items: center;
    justify-content: center;
    border-radius: 50%;
    text-align: center;
    line-height: 1.05;
    font-weight: 500;
  }
  .card--front .logo {
    left: 35px; top: 27px;
    width: 100px; height: 100px;
    border: 1px solid var(--ink-soft);
    font-size: 14px;
    color: var(--ink);
  }
  .card--back .logo {
    left: 166px; top: 50px;
    width: 184px; height: 184px;
    border: 1px solid var(--logo-ring-dark);
    font-size: 24px;
    color: var(--white);
    z-index: 2;
  }

  .staff-name {
    position: absolute;
    left: 24px; top: 128px;
    margin: 0;
    font-size: 22px;
    font-weight: 500;
    letter-spacing: 0.2px;
  }
  .divider {
    position: absolute;
    left: 24px; top: 164px;
    width: 452px; height: 1.5px;
    background: var(--rule);
  }
  .address {
    position: absolute;
    left: 24px; top: 172px;
    margin: 0;
    font-size: 13.5px;
    line-height: 18px;
    color: var(--ink-soft);
    font-style: normal;
  }
  .contacts {
    position: absolute;
    left: 24px; top: 217px;
    margin: 0; padding: 0;
    list-style: none;
    font-size: 13.5px;
    line-height: 17.5px;
    color: var(--ink-soft);
  }
  .contacts li { display: flex; align-items: center; gap: 6px; }
  .contacts svg { width: 12px; height: 12px; flex: none; }

  .corner-sketch {
    position: absolute;
    right: 0; bottom: 0;
    width: 140px; height: 122px;
  }
  .back-pattern {
    position: absolute;
    inset: 0;
    width: 100%; height: 100%;
  }
</style>
</head>
<body>
<div class="canvas">

  <section class="card card--front">
    <div class="logo">Heritage<br>Hollow</div>
    <h1 class="staff-name">Maya Torvell</h1>
    <div class="divider"></div>
    <address class="address">PO Box Glenwarra<br>NSW 2791</address>
    <ul class="contacts">
      <li>
        <svg viewBox="0 0 12 12" fill="none" stroke="#1d1f21" stroke-width="1"><circle cx="6" cy="6" r="5"/><path d="M4 3.5 L5 5 L4.6 5.6 Q5.4 7 6.6 7.5 L7.2 7 L8.6 7.9 Q8.2 9 7 8.8 Q4 8 3.2 5 Q3.2 3.8 4 3.5Z" fill="#1d1f21" stroke="none"/></svg>
        02 6481 7395
      </li>
      <li>
        <svg viewBox="0 0 12 12" fill="none" stroke="#1d1f21" stroke-width="1"><rect x="1" y="2.5" width="10" height="7"/><path d="M1 2.5 L6 6.5 L11 2.5"/></svg>
        maya@kelvadtrading.com.au
      </li>
      <li>
        <svg viewBox="0 0 12 12" fill="none" stroke="#1d1f21" stroke-width="1"><circle cx="6" cy="6" r="5"/><ellipse cx="6" cy="6" rx="2.2" ry="5"/><path d="M1 6 H11"/></svg>
        www.heritagehollow.com.au
      </li>
    </ul>
    <svg class="corner-sketch" viewBox="0 0 140 122" role="img" aria-label="Hand-drawn sketch of a roof gable corner">
      <polygon points="0,122 140,0 140,122" fill="var(--sketch-light)"/>
    </svg>
  </section>

  <section class="card card--back">
    <svg class="back-pattern" viewBox="0 0 500 285" preserveAspectRatio="none" role="img" aria-label="Faint large hand-drawn sketch of roof trusses across a black background">
      <defs>
        <linearGradient id="backTone" x1="0" y1="0" x2="1" y2="1">
          <stop offset="0" stop-color="#1f2124"/>
          <stop offset="0.5" stop-color="#111214"/>
          <stop offset="1" stop-color="#1c1d20"/>
        </linearGradient>
      </defs>
      <rect width="500" height="285" fill="url(#backTone)"/>
    </svg>
    <div class="logo">Heritage<br>Hollow</div>
  </section>

</div>
</body>
</html>
```